Veldmark Supplies Business Card

Professional business card that stand out to our potential customers. Front and back with clean modern design

Industry/Entity Type

Oil and gas

Contact Information for Business Card

Name, address, website , office phone and cell number

Requirements
Must have
• Editable files for each employee

```html
<!DOCTYPE html>
<html lang="en">
<head>
<meta charset="utf-8">
<title>Veldmark Supplies – Business Card</title>
<link rel="stylesheet" href="https://fonts.googleapis.com/css2?family=Montserrat:wght@500;600;800&family=Arimo:wght@400&display=swap">
<style>
  :root {
    --navy: #18204a;
    --navy-deep: #141b3f;
    --red: #e8262c;
    --blue: #16a9d3;
    --ink: #1f1f22;
    --paper: #eeeeee;
    --stage: #dcdcdc;
  }
  * { box-sizing: border-box; margin: 0; padding: 0; }
  html, body { width: 1200px; height: 1000px; overflow: hidden; }
  body { background: var(--stage); position: relative; font-family: "Arimo", Arial, sans-serif; }

  .card {
    position: absolute;
    width: 700px;
    height: 400px;
    box-shadow: 0 6px 18px rgba(0,0,0,0.18);
    overflow: hidden;
  }

  /* Back of card */
  .card-back {
    left: 80px; top: 60px;
    background: var(--navy);
    display: flex; align-items: center; justify-content: center;
  }
  .card-back .pattern {
    position: absolute; inset: 0;
    background: radial-gradient(circle at 50% 45%, var(--navy) 0%, var(--navy-deep) 100%);
  }
  .wordmark {
    position: relative;
    display: flex; align-items: center; gap: 12px;
    font-family: "Montserrat", sans-serif;
    font-weight: 800;
    text-transform: uppercase;
    letter-spacing: 1px;
  }
  .wordmark .mark-square { width: 22px; height: 22px; background: var(--blue); }
  .card-back .wordmark { color: #ffffff; font-size: 30px; margin-top: 20px; }

  /* Front of card */
  .card-front {
    left: 420px; top: 520px;
    background: var(--paper);
  }
  .card-front .brand-side {
    position: absolute; left: 0; top: 0; width: 330px; height: 392px;
    display: flex; align-items: center; justify-content: center;
  }
  .card-front .wordmark { color: var(--red); font-size: 24px; }
  .card-front .divider {
    position: absolute; left: 340px; top: 40px;
    width: 1.5px; height: 275px; background: var(--blue);
  }
  .details { position: absolute; left: 375px; top: 42px; }
  .person-name {
    font-family: "Montserrat", sans-serif; font-weight: 800;
    color: var(--red); font-size: 27px; letter-spacing: 1px; text-transform: uppercase;
  }
  .person-title {
    font-family: "Montserrat", sans-serif; font-weight: 500;
    color: var(--ink); font-size: 17px; letter-spacing: 1px; text-transform: uppercase;
    margin-top: 2px;
  }
  .contact-list { list-style: none; margin-top: 48px; }
  .contact-list li {
    display: flex; align-items: flex-start; gap: 10px;
    font-size: 17px; color: var(--ink); line-height: 1.3; margin-bottom: 4px;
  }
  .contact-list svg { width: 18px; height: 18px; flex: none; margin-top: 2px; fill: var(--blue); }

  .accent-band {
    position: absolute; left: 0; bottom: 0; width: 100%; height: 8px; display: flex;
  }
  .accent-band .band-blue { flex: 0 0 76%; background: var(--blue); }
  .accent-band .band-gap { flex: 0 0 4px; background: var(--paper); }
  .accent-band .band-red { flex: 1; background: var(--red); }
</style>
</head>
<body>

<section class="card card-back" aria-label="Business card back">
  <div class="pattern" role="img" aria-label="Tonal repeating brand pattern in deep navy"></div>
  <div class="wordmark"><span class="mark-square"></span><span>Veldmark Supplies</span></div>
</section>

<section class="card card-front" aria-label="Business card front">
  <div class="brand-side">
    <div class="wordmark"><span class="mark-square"></span><span>Veldmark Supplies</span></div>
  </div>
  <div class="divider"></div>
  <div class="details">
    <h1 class="person-name">Marcus Hale</h1>
    <p class="person-title">Managing Director</p>
    <ul class="contact-list">
      <li>
        <svg viewBox="0 0 24 24" aria-hidden="true"><path d="M3 8h18v13H3zM6 3h4v4H6zM14 10h5v3h-5zM5 15h3v2H5zm4 0h3v2H9zm-4 3h3v2H5zm4 0h3v2H9z"/></svg>
        <span>044-555 210 384</span>
      </li>
      <li>
        <svg viewBox="0 0 24 24" aria-hidden="true"><path d="M8 2h8a2 2 0 0 1 2 2v16a2 2 0 0 1-2 2H8a2 2 0 0 1-2-2V4a2 2 0 0 1 2-2zm0 3v13h8V5zM2 8h2v8H2zm18 0h2v8h-2z"/></svg>
        <span>011-555 873 162</span>
      </li>
      <li>
        <svg viewBox="0 0 24 24" aria-hidden="true"><path d="M22 2 2 10l7 3 2 8 3-6 6 4z"/></svg>
        <span>hello@veldmarksupply.com</span>
      </li>
      <li>
        <svg viewBox="0 0 24 24" aria-hidden="true"><path d="M12 1a8 8 0 0 0-8 8c0 6 8 14 8 14s8-8 8-14a8 8 0 0 0-8-8zm0 11a3 3 0 1 1 0-6 3 3 0 0 1 0 6z"/></svg>
        <span>4170 Harbor Ridge Pkwy,<br>212-B, FL 32509</span>
      </li>
    </ul>
  </div>
  <div class="accent-band"><span class="band-blue"></span><span class="band-gap"></span><span class="band-red"></span></div>
</section>

</body>
</html>
```